Statement on the current financial and economic crisis, with a focus on Greece,

Anybody can become angry - that is easy, but to be angry with the right person and to the right degree and at the right time and for the right purpose, and in the right way - that is not within everybody's power and is not easy.
(Pherondes ) greek philosopher

i want to do a poster with this words from Pherondes greek philosopher and to show this statement for the greek people... its about for my project that i am doing.

Target Market(s)

my audience will be greek people but not only, from 18-80 years old for that reason i want my statement to be in english.

Industry/Entity Type

Financial

Requirements
Must have
• Anybody can become angry - that is easy, but to be angry with the right person and to the right degree and at the right time and for the right purpose, and in the right way - that is not within everybody's power and is not easy.
i want to show in my poster this statement from:
Pherondes greek philosopher (384 – 322 BC)

```html
<!DOCTYPE html>
<html lang="en">
<head>
<meta charset="utf-8">
<title>Anybody Can Become Angry – Pherondes</title>
<link rel="stylesheet" href="https://fonts.googleapis.com/css2?family=Cinzel:wght@500;600;700;900&display=swap">
<style>
  :root {
    --saffron: #f8bb12;
    --flag-black: #111111;
    --flag-red: #d0001e;
    --flag-gold: #f8c400;
    --sweden-blue: #3d8fe0;
    --sweden-yellow: #fff200;
    --spain-red: #c8001a;
    --spain-yellow: #f6e020;
    --hungary-red: #c50016;
    --hungary-white: #ffffff;
    --hungary-green: #3fd200;
    --union-blue: #1a2fd0;
    --union-red: #d0101a;
    --france-blue: #2f59ff;
    --france-white: #ffffff;
    --france-red: #ff1a00;
    --greek-blue: #4ca3ec;
    --greek-light: #a9d4f6;
    --ink: #111111;
  }
  html, body { margin: 0; padding: 0; overflow: hidden; }
  .poster {
    position: relative;
    width: 849px;
    height: 1200px;
    background: var(--saffron);
    overflow: hidden;
    font-family: "Cinzel", "Times New Roman", serif;
    color: var(--ink);
  }
  .flag { position: absolute; display: block; }
  .flag-germany { left: 0; top: 32px; width: 223px; height: 141px; }
  .flag-sweden { left: 219px; top: 0; width: 342px; height: 115px; }
  .flag-hungary { left: 561px; top: 22px; width: 288px; height: 139px; }
  .flag-union { left: 0; top: 137px; width: 266px; height: 165px; }
  .flag-spain { left: 262px; top: 115px; width: 306px; height: 180px; }
  .flag-france { left: 568px; top: 161px; width: 281px; height: 192px; }
  .held-flag-illustration {
    position: absolute;
    left: 0;
    top: 262px;
    width: 790px;
    height: 480px;
    background: linear-gradient(160deg, var(--greek-light) 0%, var(--greek-blue) 100%);
  }
  .quote {
    position: absolute;
    left: 133px;
    top: 768px;
    width: 640px;
    text-align: center;
    text-transform: uppercase;
  }
  .quote-headline {
    margin: 0;
    font-weight: 900;
    font-size: 60px;
    line-height: 64px;
    letter-spacing: 1px;
  }
  .quote-body {
    margin: 8px 0 0;
    font-weight: 600;
    font-size: 22px;
    line-height: 35px;
    letter-spacing: 0.5px;
  }
  .attribution {
    margin: 10px 0 0;
    font-weight: 700;
    font-size: 25px;
    letter-spacing: 1px;
  }
  .attribution-role { font-size: 15px; font-weight: 500; }
</style>
</head>
<body>
<main class="poster">
  <svg class="flag flag-sweden" viewBox="0 0 342 115" preserveAspectRatio="none" aria-hidden="true">
    <rect width="342" height="115" fill="var(--sweden-blue)"/>
    <rect x="86" width="36" height="115" fill="var(--sweden-yellow)"/>
    <rect y="36" width="342" height="33" fill="var(--sweden-yellow)"/>
  </svg>
  <svg class="flag flag-hungary" viewBox="0 0 288 139" preserveAspectRatio="none" aria-hidden="true">
    <rect width="288" height="58" fill="var(--hungary-red)"/>
    <rect y="58" width="288" height="60" fill="var(--hungary-white)"/>
    <rect y="118" width="288" height="21" fill="var(--hungary-green)"/>
  </svg>
  <svg class="flag flag-germany" viewBox="0 0 223 141" preserveAspectRatio="none" aria-hidden="true">
    <rect width="223" height="47" fill="var(--flag-black)"/>
    <rect y="47" width="223" height="47" fill="var(--flag-red)"/>
    <rect y="94" width="223" height="47" fill="var(--flag-gold)"/>
  </svg>
  <svg class="flag flag-union" viewBox="0 0 266 165" preserveAspectRatio="none" aria-hidden="true">
    <rect width="266" height="165" fill="var(--union-blue)"/>
    <path d="M0 0 L266 165 M266 0 L0 165" stroke="#fff" stroke-width="30"/>
    <path d="M0 0 L266 165 M266 0 L0 165" stroke="var(--union-red)" stroke-width="10"/>
    <rect x="108" width="50" height="165" fill="#fff"/>
    <rect y="58" width="266" height="50" fill="#fff"/>
    <rect x="118" width="30" height="165" fill="var(--union-red)"/>
    <rect y="68" width="266" height="30" fill="var(--union-red)"/>
  </svg>
  <svg class="flag flag-spain" viewBox="0 0 306 180" preserveAspectRatio="none" aria-hidden="true">
    <rect width="306" height="45" fill="var(--spain-red)"/>
    <rect y="45" width="306" height="92" fill="var(--spain-yellow)"/>
    <rect y="137" width="306" height="43" fill="var(--spain-red)"/>
  </svg>
  <svg class="flag flag-france" viewBox="0 0 281 192" preserveAspectRatio="none" aria-hidden="true">
    <rect width="94" height="192" fill="var(--france-blue)"/>
    <rect x="94" width="94" height="192" fill="var(--france-white)"/>
    <rect x="188" width="93" height="192" fill="var(--france-red)"/>
  </svg>

  <div class="held-flag-illustration" role="img" aria-label="Illustration of a hand in a dark suit sleeve holding up a waving blue and white Greek flag"></div>

  <section class="quote">
    <h1 class="quote-headline">Anybody can<br>become angry ~</h1>
    <p class="quote-body">That is easy, but to be angry with the<br>right person and to the right degree<br>and at the right time and for the right<br>purpose, and in the right way ~<br>that is not within<br>everybody’s power and is not easy.</p>
    <p class="attribution">Pherondes <span class="attribution-role">(Greek philosopher)</span></p>
  </section>
</main>
</body>
</html>
```